KELBRIDGE PAINTING

We are a painting company. We paint residential, commercial and strata jobs. I need the website to be very sharp, neat and elegant. I've attached our logo. the Logo needs to be embossed as a gold color and the background like a Matt black. I need these tabs:

• HOME • ABOUT US • SERVICES • TESTIMONIALS • SHOWCASE • CONTACT US

Be creative and innovative in your style.
take this as an example to just get the gist of what I'm expecting. If you can better it then the job is yours!

http://rickhalvorpainting.com.au/contact.html

I look forward to seeing your artwork :)

#These are the links to my logo in PSD format.

https://www.filevaultzy.com/s/qwertplk83nd7ha/Kelbridge%20Painting%20Luxury%20Gold.rar

https://www.filevaultzy.com/sh/bzuyrak2m5wqp9/QoPL7-xvMn

Painting

• Making the Logo embossed like the artworks i have attached is definitely a necessity.

Can you let me know if this is possible to apply to the website.

thank you

```html
<!DOCTYPE html>
<html lang="en">
<head>
<meta charset="utf-8">
<title>Kelbridge Painting</title>
<link href="https://fonts.googleapis.com/css2?family=Source+Sans+3:ital,wght@0,400;0,600;0,700;1,400&display=swap" rel="stylesheet">
<style>
:root{
  --matt:#1e232b;
  --gold:#f0c050;
  --gold-deep:#d4a21a;
  --gold-mid:#e0b040;
  --gold-soft:#ecc06a;
  --sand:#f4d49a;
  --slate-1:#4b5058;
  --slate-2:#6b7078;
  --slate-3:#9a9ca0;
  --footer:#9c9ea3;
  --white:#ffffff;
  --rule:#3a4049;
}
*{margin:0;padding:0;box-sizing:border-box}
html,body{width:1054px;height:1200px;overflow:hidden}
body{position:relative;background:var(--matt);font-family:"Source Sans 3",sans-serif;color:var(--white)}
.abs{position:absolute}

.site-header{left:0;top:0;width:1054px;height:81px;background:var(--matt);border-bottom:1px solid var(--gold-deep)}
.header-phone{right:146px;top:16px;font-size:20px;font-weight:700;color:var(--gold);display:flex;align-items:center;gap:8px}
.main-nav{right:146px;top:56px;display:flex;gap:27px;font-size:12.5px;font-weight:700;letter-spacing:.6px}
.main-nav a{color:var(--white);text-decoration:none}
.main-nav a.active{color:var(--gold)}

.hero{left:0;top:81px;width:1054px;height:397px;background:linear-gradient(180deg,#7a5a44 0%,#9c7a60 40%,#6a4a36 65%,#b39a88 100%)}
.brand-strip{left:243px;top:81px;width:446px;height:35px;background:linear-gradient(90deg,#e9c46a,#f6dd8a 50%,#dcb24a);display:flex;align-items:center;padding-left:15px}
.brand-name{font-size:19.5px;font-weight:700;letter-spacing:1px;color:var(--matt)}
.brand-divider{width:1px;height:17px;background:var(--gold-deep);margin:0 12px}
.brand-tagline{font-size:15px;font-style:italic;color:var(--matt)}
.logo-disc{left:147px;top:20px;width:100px;height:100px;border-radius:50%;background:var(--matt);border:3px solid var(--gold)}
.slider-dots{right:146px;top:109px;display:flex;gap:8px}
.slider-dots span{width:8px;height:8px;background:var(--matt)}
.slider-dots span.on{background:var(--gold)}

.caption-accent-tl{left:145px;top:295px;width:49px;height:48px;background:var(--gold-mid)}
.caption-accent-br{left:584px;top:345px;width:146px;height:89px;background:var(--gold-mid)}
.caption-accent-grey{left:683px;top:303px;width:31px;height:6px;background:var(--slate-3)}
.caption{left:154px;top:303px;width:560px;height:122px;background:var(--matt);padding:16px 0 0 32px;font-size:37px;line-height:44px;color:var(--white)}

.band{left:0;width:1054px;height:8px;display:flex}
.band span{height:100%}

.welcome-title{left:145px;top:518px;font-size:37px;font-weight:700;color:var(--gold)}
.welcome-copy{left:145px;top:584px;width:492px;font-size:12.2px;line-height:24.3px}
.welcome-copy p+p{margin-top:24.3px}
.more-link{left:523px;top:953px;font-size:14.5px;font-weight:700;color:var(--gold);text-decoration:none;border-bottom:2px dotted var(--gold);line-height:16px}

.contact-title{left:688px;top:528px;font-size:23px;font-weight:700;color:var(--gold)}
.contact-table{left:689px;top:569px;width:219px;border-top:1px solid var(--rule)}
.contact-row{display:flex;border-bottom:1px solid var(--rule)}
.contact-row:last-child{border-bottom:none}
.contact-icon{width:29px;border-right:1px solid var(--rule);display:flex;justify-content:center;padding-top:10px}
.contact-text{padding:8px 0 8px 13px;font-size:11.5px;line-height:16px}
.contact-phone{font-size:18px;font-weight:600;line-height:18px;padding:10px 0 14px 13px}

.like-box{left:692px;top:782px;width:214px;height:80px;background:#3c4048;border:2px solid #70747a;border-radius:5px;padding:14px 0 0 80px;line-height:24px}
.like-box .like-line{font-size:20px}
.like-box .like-name{font-size:24px;font-weight:700;color:var(--gold)}

.footer{left:0;top:1054px;width:1054px;height:146px;background:var(--footer);color:var(--matt)}
.brands-label{left:147px;top:22px;line-height:18px}
.brands-label .b1{font-size:19px;display:block}
.brands-label .b2{font-size:13.5px;font-weight:600}
.brand-item{top:30px;font-size:22px;font-weight:700;color:var(--matt)}
.copyright{left:147px;top:110px;font-size:11.5px}
.social-dot{left:880px;top:105px;width:26px;height:26px;border-radius:50%;background:#3b5998}
</style>
</head>
<body>

<header class="site-header abs">
  <div class="header-phone abs">
    <svg width="18" height="18" viewBox="0 0 24 24" aria-hidden="true"><path fill="#f0c050" d="M6.6 10.8c1.4 2.8 3.8 5.1 6.6 6.6l2.2-2.2c.3-.3.7-.4 1-.2 1.1.4 2.3.6 3.6.6.6 0 1 .4 1 1V20c0 .6-.4 1-1 1C10.6 21 3 13.4 3 4c0-.6.4-1 1-1h3.5c.6 0 1 .4 1 1 0 1.2.2 2.4.6 3.6.1.3 0 .7-.2 1z"/></svg>
    1300 47 19 32
  </div>
  <nav class="main-nav abs">
    <a class="active" href="#">HOME</a><a href="#">ABOUT US</a><a href="#">SERVICES</a><a href="#">TESTIMONIALS</a><a href="#">SHOWCASE</a><a href="#">CONTACT US</a>
  </nav>
</header>

<div class="hero abs" role="img" aria-label="Photograph of a modern living room with a brown and cream leather sectional sofa"></div>

<div class="brand-strip abs">
  <span class="brand-name">KELBRIDGE PAINTING</span>
  <span class="brand-divider"></span>
  <span class="brand-tagline">Painting Australia Everyday!</span>
</div>
<div class="logo-disc abs"></div>

<div class="slider-dots abs"><span></span><span></span><span></span><span class="on"></span></div>

<div class="caption-accent-tl abs"></div>
<div class="caption-accent-br abs"></div>
<div class="caption abs">We paint residential,<br>commercial and strata jobs</div>
<div class="caption-accent-grey abs"></div>

<div class="band abs" style="top:478px">
  <span style="width:252px;background:var(--matt)"></span>
  <span style="width:72px;background:var(--slate-1)"></span>
  <span style="width:80px;background:var(--slate-2)"></span>
  <span style="width:124px;background:var(--slate-3)"></span>
  <span style="width:106px;background:var(--gold-deep)"></span>
  <span style="width:72px;background:var(--gold-mid)"></span>
  <span style="width:80px;background:var(--gold-soft)"></span>
  <span style="width:268px;background:var(--sand)"></span>
</div>

<h1 class="welcome-title abs">Welcome!</h1>
<div class="welcome-copy abs">
  <p>Lorem ipsum dolor sit amet, consectetur adipiscing elit. Quantum Aristoxeni ingenium consumptum videmus in musicis? Nihil enim hoc differt. Re mihi non aeque satisfacit, et quidem locis pluribus. At iste non dolendi status non vocatur voluptas. Quamquam haec quidem praeposita recte et reiecta dicere licebit.</p>
  <p>Duo Reges: constructio interrete. Inde sermone vario sex illa a Dipylo stadia confecimus. Ad quorum et cognitionem et usum iam corroborati natura ipsa praeeunte deducimur. Idem iste, inquam, de voluptate quid sentit? Septem autem illi non suo, sed populorum suffragio omnium nominati sunt. Quamquam haec quidem praeposita recte et reiecta dicere licebit. Atqui eorum nihil est eius generis, ut sit in fine atque extrerno bonorum.</p>
  <p>Atqui reperies, inquit, in hoc quidem pertinacem; Sin autem est in ea, quod quidam volunt, nihil impedit hanc nostram comprehensionem summi boni. Urgent tamen et nihil remittunt. Avaritiamne minuis.</p>
</div>
<a class="more-link abs" href="#">MORE ABOUT US</a>

<h2 class="contact-title abs">Contact us</h2>
<div class="contact-table abs">
  <div class="contact-row">
    <div class="contact-icon"><svg width="16" height="20" viewBox="0 0 16 20" aria-hidden="true"><path fill="#8a8e95" d="M7 0h2v20H7zM1 3h13l2 2-2 2H1zM2 9h12v4H2l-2-2z"/></svg></div>
    <div class="contact-text">Lorem ipsum dolor sit amet consectetur adipiscing elit Quantum Aristoxeni ingenium consumptum.</div>
  </div>
  <div class="contact-row">
    <div class="contact-icon"><svg width="16" height="16" viewBox="0 0 24 24" aria-hidden="true"><path fill="#8a8e95" d="M6.6 10.8c1.4 2.8 3.8 5.1 6.6 6.6l2.2-2.2c.3-.3.7-.4 1-.2 1.1.4 2.3.6 3.6.6.6 0 1 .4 1 1V20c0 .6-.4 1-1 1C10.6 21 3 13.4 3 4c0-.6.4-1 1-1h3.5c.6 0 1 .4 1 1 0 1.2.2 2.4.6 3.6.1.3 0 .7-.2 1z"/></svg></div>
    <div class="contact-phone">1300 47 19 32</div>
  </div>
  <div class="contact-row">
    <div class="contact-icon"><svg width="17" height="12" viewBox="0 0 17 12" aria-hidden="true"><rect width="17" height="12" fill="#8a8e95"/><path d="M0 0l8.5 7L17 0" fill="none" stroke="#1e232b" stroke-width="1.2"/></svg></div>
    <div class="contact-text">mail@kelbridgepainting.com.au</div>
  </div>
</div>

<div class="like-box abs">
  <div class="like-line">Like us on</div>
  <div class="like-name">Huddlr</div>
</div>

<div class="band abs" style="top:1046px">
  <span style="width:268px;background:var(--sand)"></span>
  <span style="width:80px;background:var(--gold-soft)"></span>
  <span style="width:72px;background:var(--gold-mid)"></span>
  <span style="width:106px;background:var(--gold-deep)"></span>
  <span style="width:124px;background:var(--slate-3)"></span>
  <span style="width:80px;background:var(--slate-2)"></span>
  <span style="width:72px;background:var(--slate-1)"></span>
  <span style="width:252px;background:var(--matt)"></span>
</div>

<footer class="footer abs">
  <div class="brands-label abs"><span class="b1">BRANDS</span><span class="b2">USED BY US</span></div>
  <span class="brand-item abs" style="left:280px">Corvane</span>
  <span class="brand-item abs" style="left:416px">Pellwick</span>
  <span class="brand-item abs" style="left:556px">Tarnsby</span>
  <span class="brand-item abs" style="left:750px">Veltrashield</span>
  <div class="copyright abs">Copyright @ 2013 Kelbridge Painting. All rights reserved.</div>
  <div class="social-dot abs"></div>
</footer>

</body>
</html>
```